Casino with the 'highest winning percentage' needs a stationery design

This is for a casino in Colombo, Sri Lanka and we need a stationery design for business card, letter head and envelope.

Should be very professional, simple and elegant without fancy fonts

Reason: Not fully satisfied with the designs. Need more designs.

Business

• 1. card deck symbol 'CLUBS' in red, or black

2. name in BLOCK CAPITAL LETTERS

3. Preferred font colours are black, white or red

4. Prefer 'professional /elegant' fonts
• SHOULD NOT HAVE ANY OTHER SYMBOL EXCEPT 'CLUBS'

DO NOT PREFER ITALIC FONTS

```html
<!DOCTYPE html>
<html lang="en">
<head>
<meta charset="utf-8">
<title>Marlow's Entertainment – Business Card</title>
<link rel="stylesheet" href="https://fonts.googleapis.com/css2?family=Arimo:wght@400;700&display=swap">
<style>
  :root {
    --stage: #1d1d1f;
    --card-white: #fbfbfb;
    --card-dark: #1a1a1a;
    --card-dark-edge: #2a2a2a;
    --casino-red: #8e0a14;
    --casino-red-light: #c32a36;
    --ink: #2b2b2b;
    --ink-soft: #4a4a4a;
    --rule: #555555;
    --brand-grey: #3a3a3a;
    --brand-silver: #bdbdbd;
  }
  * { box-sizing: border-box; margin: 0; padding: 0; }
  html, body { width: 1200px; height: 890px; overflow: hidden; }
  body {
    background: var(--stage);
    position: relative;
    font-family: "Arimo", Arial, sans-serif;
  }
  .card {
    position: absolute;
    top: 145px;
    width: 360px;
    height: 600px;
    border-radius: 26px;
    overflow: hidden;
  }
  .brand-name {
    font-family: "Arimo", Arial, sans-serif;
    font-weight: 400;
    letter-spacing: 3px;
    text-align: center;
    line-height: 1.25;
  }
  /* Back of card */
  .card--back {
    left: 150px;
    background: linear-gradient(180deg, var(--card-dark-edge), var(--card-dark));
  }
  .card--back .brand-name {
    position: absolute;
    top: 70px;
    left: 0;
    right: 0;
    font-size: 20px;
    color: var(--brand-silver);
  }
  .card--back .feature-art {
    position: absolute;
    left: 0;
    right: 0;
    bottom: 0;
    height: 300px;
    background: radial-gradient(ellipse at 50% 20%, var(--casino-red-light), var(--casino-red) 70%);
  }
  /* Front of card */
  .card--front {
    left: 690px;
    background: var(--card-white);
    color: var(--ink);
    text-align: center;
  }
  .brand-dot {
    display: block;
    width: 54px;
    height: 54px;
    margin: 64px auto 22px;
    border-radius: 50%;
    background: var(--casino-red-light);
  }
  .card--front .brand-name {
    font-size: 26px;
    color: var(--brand-grey);
  }
  .person { margin-top: 52px; }
  .person .full-name {
    font-weight: 700;
    font-size: 17px;
    letter-spacing: 1px;
    color: var(--ink);
  }
  .person .role { font-size: 13px; color: var(--ink-soft); margin-top: 4px; }
  .contact {
    font-size: 13px;
    line-height: 1.4;
    color: var(--ink-soft);
  }
  .contact--phone { margin-top: 32px; }
  .contact--phone b { color: var(--ink); }
  .divider {
    width: 180px;
    height: 1px;
    margin: 14px auto;
    background: var(--rule);
  }
  .website { font-size: 14px; color: var(--ink-soft); }
  .website b { color: var(--ink); }
</style>
</head>
<body>
  <article class="card card--back">
    <p class="brand-name">MARLOW'S<br>ENTERTAINMENT</p>
    <div class="feature-art" role="img" aria-label="Large glossy red card-suit decoration"></div>
  </article>

  <article class="card card--front">
    <span class="brand-dot"></span>
    <p class="brand-name">MARLOW'S<br>ENTERTAINMENT</p>
    <div class="person">
      <p class="full-name">DANIEL FERNHILL</p>
      <p class="role">General Manager</p>
    </div>
    <div class="contact contact--phone">
      <p><b>Tel:</b> + 94 11 2408765</p>
      <p><b>Fax:</b> + 94 11 2408766</p>
    </div>
    <div class="divider"></div>
    <div class="contact">
      <p>52, Lotus Garden Mawatha</p>
      <p>Colombo 01000, Sri Lanka</p>
    </div>
    <div class="divider"></div>
    <p class="website">www.<b>marlowscolombo</b>.com</p>
  </article>
</body>
</html>
```